RW Framewell Inc Business cards

We need business cards using our existing logo but slightly modified. Right now the logo says RW Loadbearing Masonry. We want to keep the RW part of the design, but replace the Structural Concrete portion with "FRAMEWELL". Please see the attached file.
Ideally this would be a blank template so we can add Different Names, titles, and phone numbers later.
On the one side we want only the logo and on the other side the detail. I'm attaching an example for you to see.
Please reach out with any other questions. Our address and other details will be given out once we find a design we like.

Target Market(s)

Construction Industry

```html
<!DOCTYPE html>
<html lang="en">
<head>
<meta charset="utf-8">
<title>RW Framewell Inc Business Cards</title>
<link href="https://fonts.googleapis.com/css2?family=Roboto:wght@400;500;700&display=swap" rel="stylesheet">
<style>
  :root {
    --brand-blue: #2c5fa3;
    --brand-grey: #707274;
    --paper: #f6f6f5;
    --ink: #4a4a4a;
    --backdrop: #5a82bd;
    --white: #ffffff;
  }
  * { margin: 0; padding: 0; box-sizing: border-box; }
  html, body {
    width: 1200px; height: 852px; overflow: hidden;
    background: var(--backdrop);
    font-family: "Roboto", Arial, sans-serif;
  }
  .stage {
    position: relative; width: 1200px; height: 852px;
    display: flex; align-items: center; justify-content: center; gap: 50px;
  }
  .card {
    position: relative; width: 525px; height: 300px;
    border-radius: 22px; overflow: hidden;
    box-shadow: 0 6px 18px rgba(20, 40, 80, 0.3);
  }
  .card-front { background: var(--brand-blue); }
  .card-back { background: var(--paper); }

  .wordmark {
    position: absolute; display: flex; flex-direction: column; align-items: center;
    font-weight: 700; line-height: 1;
  }
  .wordmark-initials { font-size: 96px; letter-spacing: 2px; }
  .wordmark-name { font-size: 26px; letter-spacing: 7px; margin-top: 4px; }
  .card-front .wordmark {
    color: var(--white); left: 50%; top: 50%; transform: translate(-50%, -50%);
  }
  .card-back .wordmark {
    color: var(--brand-blue); left: 50px; top: 118px;
  }
  .card-back .wordmark-initials { font-size: 78px; }
  .card-back .wordmark-name { font-size: 21px; letter-spacing: 6px; }

  .swoosh { position: absolute; inset: 0; width: 100%; height: 100%; }

  .holder {
    position: absolute; right: 28px; top: 22px; text-align: right;
  }
  .holder-name { font-size: 21px; font-weight: 700; color: var(--brand-blue); }
  .holder-title { font-size: 12px; color: var(--ink); margin-top: 2px; }
  .holder-address {
    font-size: 13px; color: var(--ink); margin-top: 12px; line-height: 1.35;
  }

  .contact-list {
    position: absolute; right: 28px; bottom: 50px; list-style: none;
    text-align: right; color: var(--white); font-size: 13px; line-height: 1.55;
  }
  .contact-list li { display: flex; align-items: center; justify-content: flex-end; gap: 6px; }
  .contact-list svg { width: 11px; height: 11px; fill: var(--white); }
</style>
</head>
<body>
<main class="stage">
  <section class="card card-front" aria-label="Card front">
    <div class="wordmark">
      <span class="wordmark-initials">RW</span>
      <span class="wordmark-name">FRAMEWELL</span>
    </div>
  </section>

  <section class="card card-back" aria-label="Card back">
    <svg class="swoosh" viewBox="0 0 525 300" preserveAspectRatio="none" aria-hidden="true">
      <path d="M95 300 C 245 292, 245 135, 525 122 L 525 300 Z" fill="var(--brand-grey)"/>
      <path d="M108 300 C 252 294, 258 142, 525 132 L 525 300 Z" fill="var(--paper)"/>
      <path d="M120 300 C 260 295, 270 150, 525 142 L 525 300 Z" fill="var(--brand-blue)"/>
    </svg>

    <div class="wordmark">
      <span class="wordmark-initials">RW</span>
      <span class="wordmark-name">FRAMEWELL</span>
    </div>

    <div class="holder">
      <p class="holder-name">Daniel Hart</p>
      <p class="holder-title">Managing Director</p>
      <p class="holder-address">78 Sample Ave., Any Town,<br>Oregon, US 970001</p>
    </div>

    <ul class="contact-list">
      <li>555-014-2290
        <svg viewBox="0 0 24 24"><path d="M6.6 10.8a15.1 15.1 0 0 0 6.6 6.6l2.2-2.2a1 1 0 0 1 1-.25 11.4 11.4 0 0 0 3.6.57 1 1 0 0 1 1 1V20a1 1 0 0 1-1 1A17 17 0 0 1 3 4a1 1 0 0 1 1-1h3.5a1 1 0 0 1 1 1c0 1.25.2 2.45.57 3.57a1 1 0 0 1-.25 1z"/></svg>
      </li>
      <li>framewell.example
        <svg viewBox="0 0 24 24"><path d="M2 5h20v14H2z M2 5l10 8 10-8" fill="none" stroke="#fff" stroke-width="2"/></svg>
      </li>
      <li>daniel@framewell.example
        <svg viewBox="0 0 24 24"><circle cx="12" cy="12" r="9" fill="none" stroke="#fff" stroke-width="2"/><path d="M3 12h18M12 3c3 3 3 15 0 18M12 3c-3 3-3 15 0 18" fill="none" stroke="#fff" stroke-width="1.6"/></svg>
      </li>
    </ul>
  </section>
</main>
</body>
</html>
```